Business Card Update, need to bring life to the card, two sided color

We need a new business card design, are moving and changing addresses and need a new look, we have the logos already attached but need a new style moving forward. Can incorporate the color of the logo (The Green) as well, maybe a solid back? We deal with safety products revolving around static electricity and safety lighting. Would like to keep same font in second logo as well.

Target Market(s)

Electrical Safety, Lighting

Contact Information for Business Card

Dale Fenwick
Vice President
Office: 770-555-4821
Cell: 770-555-3067
dale@tkfenwick.example
www.tkfenwick.example
4700 West Harbor Boulevard
Suite #150
Roswell, GA 30076

Font styles to use
Serif
Sans Serif

Requirements
Must have
• Since 1918
Nice to have
• Could use the 100 Year Logo for back of card, would like the back of card to be the same green as logo.
Should not have
• No black cards please.

```html
<!DOCTYPE html>
<html lang="en">
<head>
<meta charset="UTF-8">
<title>T.K. Fenwick Business Card</title>
<link href="https://fonts.googleapis.com/css2?family=Arimo:wght@400;700&display=swap" rel="stylesheet">
<style>
  :root {
    --green: #0f9a5a;
    --green-deep: #0c8a50;
    --card-light: #ffffff;
    --stage: #e6e8e7;
    --text-light: #ffffff;
    --text-soft: #e3f3ea;
  }
  * { box-sizing: border-box; margin: 0; padding: 0; }
  html, body { width: 1200px; height: 800px; overflow: hidden; }
  body {
    background: var(--stage);
    font-family: "Arimo", Arial, sans-serif;
    position: relative;
  }
  .card {
    position: absolute;
    top: 251px;
    width: 520px;
    height: 298px;
    border-radius: 4px;
    box-shadow: 0 10px 28px rgba(0,0,0,0.18);
    overflow: hidden;
  }
  .card-front { left: 50px; background: var(--card-light); }
  .card-back { left: 630px; background: var(--green-deep); }

  /* Front */
  .front-lockup {
    position: absolute;
    left: 70px; top: 104px;
    display: flex; align-items: center; gap: 22px;
  }
  .mark-circle {
    width: 90px; height: 90px; border-radius: 50%;
    background: var(--green); flex: none;
  }
  .company-name {
    color: var(--green);
    font-weight: 700;
    font-size: 38px;
    line-height: 1;
  }
  .company-sub {
    color: var(--green);
    font-weight: 700;
    font-size: 17px;
    margin-top: 4px;
  }

  /* Back */
  .back-details {
    position: absolute;
    left: 30px; top: 24px;
    width: 300px;
    color: var(--text-light);
  }
  .back-details .company-name { color: var(--text-light); font-size: 26px; }
  .back-details .company-sub { color: var(--text-soft); font-size: 12px; margin-top: 3px; }
  .person { margin-top: 14px; font-size: 13px; white-space: nowrap; }
  .person-name { font-weight: 700; font-size: 20px; }
  .person-role { color: var(--text-soft); }
  .address { margin-top: 8px; font-size: 12.5px; line-height: 1.4; color: var(--text-soft); }
  .contact-list { list-style: none; margin-top: 8px; font-size: 12.5px; line-height: 1.6; }
  .contact-list li { display: flex; align-items: center; gap: 8px; white-space: nowrap; }
  .contact-list svg { width: 13px; height: 13px; flex: none; }

  .back-mark {
    position: absolute;
    right: 34px; top: 40px;
    width: 160px;
    display: flex; flex-direction: column; align-items: center; gap: 12px;
  }
  .back-mark .mark-circle { width: 150px; height: 150px; background: var(--card-light); }
  .back-mark .mark-name {
    color: var(--text-light);
    font-weight: 700;
    font-size: 20px;
  }
  .since {
    color: var(--text-soft);
    font-size: 13px;
    letter-spacing: 2px;
    text-transform: uppercase;
    margin-top: -6px;
  }
</style>
</head>
<body>
  <section class="card card-front" aria-label="Business card front">
    <div class="front-lockup">
      <div class="mark-circle" aria-hidden="true"></div>
      <div>
        <div class="company-name">T.K. Fenwick</div>
        <div class="company-sub">Manufacturing Company, Inc.</div>
      </div>
    </div>
  </section>

  <section class="card card-back" aria-label="Business card back">
    <div class="back-details">
      <div class="company-name">T.K. Fenwick</div>
      <div class="company-sub">Manufacturing Company, Inc.</div>
      <div class="person"><span class="person-name">Dale Fenwick</span> <span class="person-role">| Vice President</span></div>
      <div class="address">4700 West Harbor Boulevard, Suite #150<br>Roswell, GA 30076</div>
      <ul class="contact-list">
        <li>
          <svg viewBox="0 0 14 14" aria-hidden="true"><path d="M3 1.5 L5.5 1.5 L6.5 4.5 L5 5.5 C5.8 7.3 6.7 8.2 8.5 9 L9.5 7.5 L12.5 8.5 L12.5 11 C12.5 12 11.5 12.8 10.5 12.5 C6 11.5 2.5 8 1.5 3.5 C1.2 2.5 2 1.5 3 1.5 Z" fill="var(--text-light)"/></svg>
          Office: 770-555-4821
        </li>
        <li>
          <svg viewBox="0 0 14 14" aria-hidden="true"><rect x="3" y="1" width="8" height="12" rx="1.5" fill="none" stroke="var(--text-light)" stroke-width="1.6"/></svg>
          Cell: 770-555-3067
        </li>
        <li>
          <svg viewBox="0 0 14 14" aria-hidden="true"><rect x="1" y="3" width="12" height="8" fill="var(--text-light)"/><path d="M1 3 L7 8 L13 3" fill="none" stroke="var(--green-deep)" stroke-width="1.2"/></svg>
          dale@tkfenwick.example
        </li>
        <li>
          <svg viewBox="0 0 14 14" aria-hidden="true"><circle cx="7" cy="7" r="6" fill="var(--text-light)"/><path d="M1 7 H13 M7 1 V13 M7 1 C3.5 4 3.5 10 7 13 M7 1 C10.5 4 10.5 10 7 13" fill="none" stroke="var(--green-deep)" stroke-width="0.9"/></svg>
          www.tkfenwick.example
        </li>
      </ul>
    </div>
    <div class="back-mark">
      <div class="mark-circle" aria-hidden="true"></div>
      <div class="mark-name">T.K. Fenwick</div>
      <div class="since">Since 1918</div>
    </div>
  </section>
</body>
</html>
```